The (Private) News Sharing Report

This is a professional and academic report of 35 pages for journalists and teachers. The topic of the report is News Sharing: journalism, social networks and technology. Attached there is an example of the kind of design we are looking for: visual, fresh and modern.

Target Market(s)

Journalists, Journalism Students, Communication Researchers,

Industry/Entity Type

Media

Font styles to use
Sans Serif

Colors
3276b5
33a6d7
886aae
b868aa

Requirements
Must have
• Copyleft images, visual style
Nice to have
• There is an example attached.

```html
<!DOCTYPE html>
<html lang="en">
<head>
<meta charset="utf-8">
<title>The (Private) News Sharing Report — Page Layouts</title>
<link href="https://fonts.googleapis.com/css2?family=Poppins:ital,wght@0,400;0,500;0,600;0,700;1,400&family=Open+Sans:wght@400;600;700&display=swap" rel="stylesheet">
<style>
:root{
  --sky:#45acdf;
  --sky-light:#a9d9f1;
  --blue:#2b8ccb;
  --ink:#2c2c2c;
  --body:#4a4a4a;
  --row:#e6e6e6;
  --sheet:#c9c9c9;
  --stage:#3e3e3e;
  --white:#ffffff;
  --art-a:#bfe3f5;
  --art-b:#e9a6c8;
}
*{margin:0;padding:0;box-sizing:border-box}
html,body{width:1200px;height:3922px;overflow:hidden}
body{background:var(--sheet);font-family:"Open Sans",sans-serif;color:var(--body);position:relative}

.cover-strip{position:absolute;left:0;top:0;width:1200px;height:746px;background:var(--stage)}
.cover-thumb{position:absolute;top:137px;width:333px;height:471px;overflow:hidden}
.cover-thumb .page{transform:scale(.68);transform-origin:0 0;box-shadow:none}

.label{position:absolute;width:490px;text-align:center;font-family:"Poppins",sans-serif;font-weight:500;font-size:22px;letter-spacing:.5px;color:#1e1e1e}

.page{position:absolute;width:490px;height:692px;background:var(--white);overflow:hidden;box-shadow:0 2px 8px rgba(0,0,0,.18)}
.page .rule{position:absolute;left:67px;top:0;width:3px;height:183px;background:var(--sky)}
.page .wave{position:absolute;left:0;bottom:0;width:490px;height:130px}
.page .footer{position:absolute;left:18px;right:18px;bottom:12px;display:flex;justify-content:space-between;font-family:"Poppins",sans-serif;font-size:7.5px;color:var(--white);letter-spacing:.2px}
.page .footer b{font-weight:700}
.text{position:absolute;font-size:8.2px;line-height:1.42;color:var(--body)}
.text p{margin-bottom:9px;text-align:justify}
.heading{position:absolute;font-family:"Poppins",sans-serif;font-weight:700;color:var(--blue);font-size:28px;letter-spacing:-.3px}
.subhead{font-family:"Poppins",sans-serif;font-weight:600;color:var(--sky);font-size:10px;margin:4px 0 3px}
.art{position:absolute;border-radius:6px}

/* cover */
.cover .band{position:absolute;left:0;top:0;width:490px;height:300px}
.cover .kicker{position:absolute;top:62px;width:100%;text-align:center;font-family:"Poppins",sans-serif;font-size:21px;color:var(--white);font-weight:400}
.cover .title{position:absolute;top:86px;width:100%;text-align:center;font-family:"Poppins",sans-serif;font-size:40px;font-weight:700;color:var(--white);letter-spacing:-.3px}
.cover .sub{position:absolute;top:142px;width:100%;text-align:center;font-family:"Poppins",sans-serif;font-size:16px;line-height:1.3;color:var(--white)}
.cover .byline{position:absolute;top:540px;width:100%;text-align:center;font-size:11px;line-height:1.4;color:var(--ink)}
.cover .byline strong{font-family:"Poppins",sans-serif;font-weight:700;font-size:11px}
.cover .byline em{font-style:italic}
.cover .year{position:absolute;top:610px;width:100%;text-align:center;font-family:"Poppins",sans-serif;font-size:40px;font-weight:700;color:var(--sky)}

/* credits */
.credit-lead{position:absolute;left:85px;top:148px;font-family:"Poppins",sans-serif;font-size:12px;line-height:1.35;color:var(--ink)}
.credit-lead b{color:var(--sky);font-weight:600}

/* tables */
.toc{position:absolute;left:63px;width:370px;list-style:none}
.toc li{display:flex;justify-content:space-between;align-items:center;font-family:"Poppins",sans-serif;font-size:8.5px;line-height:13px;padding:3px 18px;color:var(--ink);margin-bottom:8px}
.toc li:nth-child(odd){background:var(--row)}
.toc li.strong{font-weight:700}
.toc.plain li{padding:3px 6px;margin-bottom:11px;font-size:8px}

/* interview */
.photo{position:absolute;left:85px;top:76px;width:82px;height:82px;background:linear-gradient(135deg,#c49a6c,#8a5a3b)}
.person{position:absolute;left:85px;top:170px;font-family:"Poppins",sans-serif;font-weight:700;font-size:16px;color:var(--blue)}
.role{position:absolute;left:85px;top:192px;font-size:7.5px;font-style:italic;line-height:1.4;color:var(--body)}
.quote{position:absolute;left:85px;right:50px;top:240px;font-family:"Poppins",sans-serif;font-size:10.5px;line-height:1.45;color:var(--ink);text-align:center}
.quote .mark{color:var(--sky);font-weight:700;font-size:22px;line-height:0;vertical-align:-8px}
</style>
</head>
<body>

<svg width="0" height="0" style="position:absolute" aria-hidden="true">
  <defs>
    <symbol id="footer-wave" viewBox="0 0 490 130" preserveAspectRatio="none">
      <path d="M0 40 C90 0 170 10 250 55 C330 95 410 70 490 20 L490 130 L0 130 Z" fill="#a9d9f1"/>
      <path d="M0 55 C80 20 170 30 250 75 C330 110 420 95 490 55 L490 130 L0 130 Z" fill="#45acdf"/>
    </symbol>
    <symbol id="cover-wave" viewBox="0 0 490 300" preserveAspectRatio="none">
      <path d="M0 0 H490 V180 C420 150 360 210 280 225 C190 240 120 195 0 215 Z" fill="#a9d9f1"/>
      <path d="M0 0 H490 V165 C420 140 360 195 280 208 C190 222 120 180 0 200 Z" fill="#45acdf"/>
    </symbol>
  </defs>
</svg>

<!-- cover series -->
<section class="cover-strip">
  <div class="cover-thumb" style="left:50px">
    <div class="page cover" style="left:0;top:0">
      <svg class="band"><use href="#cover-wave"/></svg>
      <div class="kicker">THE (PRIVATE) NEWS</div>
      <div class="title">SHARING REPORT</div>
      <div class="sub">A starting guide for<br>researchers and journalists</div>
      <div class="art" role="img" aria-label="Illustration of a person editing a giant text document on a laptop beside stacked books" style="left:80px;top:225px;width:330px;height:290px;background:linear-gradient(135deg,var(--art-a),var(--art-b))"></div>
      <div class="byline"><strong>A REPORT BY TOMÁS ELÍAS RIVERA-LUND</strong><br><em>Visiting Scholar at the Capital City University (Easton, USA)<br>with the help of Research Grants 18/19 from Northbridge University<br>of Valdoria (Valdoria, Spain)</em></div>
      <div class="year">2019</div>
    </div>
  </div>
  <div class="cover-thumb" style="left:433px">
    <div class="page cover" style="left:0;top:0">
      <svg class="band"><use href="#cover-wave"/></svg>
      <div class="kicker">THE (PRIVATE) NEWS</div>
      <div class="title">SHARING REPORT</div>
      <div class="sub">A starting guide for<br>researchers and journalists</div>
      <div class="art" role="img" aria-label="Illustration of a person editing a giant text document on a laptop beside stacked books" style="left:80px;top:225px;width:330px;height:290px;background:linear-gradient(135deg,var(--art-a),var(--art-b))"></div>
      <div class="byline"><strong>A REPORT BY TOMÁS ELÍAS RIVERA-LUND</strong><br><em>Visiting Scholar at the Capital City University (Easton, USA)<br>with the help of Research Grants 18/19 from Northbridge University<br>of Valdoria (Valdoria, Spain)</em></div>
      <div class="year">2019</div>
    </div>
  </div>
  <div class="cover-thumb" style="left:816px">
    <div class="page cover" style="left:0;top:0">
      <svg class="band"><use href="#cover-wave"/></svg>
      <div class="kicker">THE (PRIVATE) NEWS</div>
      <div class="title">SHARING REPORT</div>
      <div class="sub">A starting guide for<br>researchers and journalists</div>
      <div class="art" role="img" aria-label="Illustration of a person editing a giant text document on a laptop beside stacked books" style="left:80px;top:225px;width:330px;height:290px;background:linear-gradient(135deg,var(--art-a),var(--art-b))"></div>
      <div class="byline"><strong>A REPORT BY TOMÁS ELÍAS RIVERA-LUND</strong><br><em>Visiting Scholar at the Capital City University (Easton, USA)<br>with the help of Research Grants 18/19 from Northbridge University<br>of Valdoria (Valdoria, Spain)</em></div>
      <div class="year">2019</div>
    </div>
  </div>
</section>

<!-- row 1 -->
<div class="label" style="left:108px;top:828px">COVER PAGE</div>
<div class="label" style="left:615px;top:828px">INNER PAGE 1</div>

<article class="page cover" style="left:108px;top:871px">
  <svg class="band"><use href="#cover-wave"/></svg>
  <div class="kicker">THE (PRIVATE) NEWS</div>
  <div class="title">SHARING REPORT</div>
  <div class="sub">A starting guide for<br>researchers and journalists</div>
  <div class="art" role="img" aria-label="Illustration of a person editing a giant text document on a laptop beside stacked books" style="left:80px;top:225px;width:330px;height:290px;background:linear-gradient(135deg,var(--art-a),var(--art-b))"></div>
  <div class="byline"><strong>A REPORT BY TOMÁS ELÍAS RIVERA-LUND</strong><br><em>Visiting Scholar at the Capital City University (Easton, USA)<br>with the help of Research Grants 18/19 from Northbridge University<br>of Valdoria (Valdoria, Spain)</em></div>
  <div class="year">2019</div>
</article>

<article class="page" style="left:615px;top:871px">
  <div class="rule"></div>
  <div class="credit-lead">This is a report by<br><b>TOMÁS ELÍAS RIVERA-LUND (PHD),</b></div>
  <div class="text" style="left:65px;top:214px;width:355px">
    <p>a journalist working at Northbridge University of Valdoria (NBU, Spain), where he is the Head of the Communication Sciences Department. This project has been supported by a research grant from NBU to do a research stay as a Visiting Scholar at the Capital City University (CCU), USA, and the help of professor Laura Bennett at CCU.</p>
    <p>Special thanks goes to those who collaborated in the interviews: the journalists at the Global Forum for Reporters (GFR), The Harbor Ledger, Meridian Media Network, Sol Noticias, The Center for Open Accountability, The Iberia Brief, Factora and Verdad Lab. In addition, I also want to thank the whole faculty members at the School of Communication at the Capital City University, who always offered their collaboration.</p>
    <p>Special thanks also goes to colleagues and scholars who selflessly dedicated their time to talk and hold meetings. They shed light on many topics reflected in to go through the report in depth. They are Pablo Arriaga, Omar Haddad, Elena Quintero, Ruth Castell, Dana Whitlock, Rafa Morell, Victor Ashby, and Helen Doyle.</p>
    <p>The interviews are expressions of personal opinions as journalists and they do not necessarily express the official point of view of the media where they work. Inquiries for further information about this research can be sent to trivera@examplemail.com or trivera@nbu.example</p>
  </div>
  <svg class="wave"><use href="#footer-wave"/></svg>
  <div class="footer"><span>THE (PRIVATE) NEWS <b>SHARING REPORT</b></span><span>PAGE - 2</span></div>
</article>

<!-- row 2 -->
<article class="page" style="left:108px;top:1584px">
  <div class="rule"></div>
  <div class="heading" style="left:85px;top:150px">INDEX</div>
  <ul class="toc" style="top:212px">
    <li class="strong"><span>INTRODUCTION</span><span>4</span></li>
    <li class="strong"><span>RESEARCH QUESTIONS</span><span>5</span></li>
    <li><span>1. The Media Landscape</span><span>6</span></li>
    <li><span>2. The Interviews</span><span>11</span></li>
    <li><span>3. The Best Practices</span><span>29</span></li>
    <li><span>4. Conclusions</span><span>31</span></li>
    <li><span>5. References</span><span>33</span></li>
  </ul>
  <div class="art" role="img" aria-label="Illustration of a hand holding a smartphone with a reporter and floating chat, rating and like icons" style="left:205px;top:425px;width:225px;height:250px;background:linear-gradient(160deg,var(--art-a),#f2c3a2)"></div>
  <svg class="wave"><use href="#footer-wave"/></svg>
  <div class="footer"><span>THE (PRIVATE) NEWS <b>SHARING REPORT</b></span><span>PAGE - 3</span></div>
</article>

<article class="page" style="left:615px;top:1584px">
  <div class="rule"></div>
  <div class="heading" style="left:85px;top:116px">INTRODUCTION</div>
  <div class="text" style="left:82px;top:164px;width:355px;font-size:7.6px">
    <p>The job of journalists is not just longer on the internet because it ends later, it is also longer because it starts before. On the internetweb, on the one hand, a journalist can have a community even before having a journalistic product. On the other hand, social recommendations, incidental consumption of news and online private messages are giving a broader reach to journalism, as we know it now.</p>
    <p>Because publishing is not the end of the journalistic routine, the whole process now is longer. You cannot fully understand what "news" means for people if you do not understand how and why they are sharing the news on online private platforms. Private messaging networks are adding new challenges to journalists and the media. When we are talking about online private environments, issues such as sources, fact-checking, misinformation, privacy or (fake) news are being redefined, as well as the notions of trust, community, public service and media literacy.</p>
    <p>In 2018 the presidential candidate Marco Silvano was accused of running a whole fake news campaign through ChatLine with hundreds of millions of messages against his opponent. This scandal is just an example of the growing relevance of fact-checking and the need to for media literacy skills among users of private messaging networks.</p>
    <p>Many news sites added a ChatLine sharing option in their news during the last few years (Marlow, 2014) and it seems like private channels, such as this one, could become a "major traffic driver for news sites" (Hartmann, A., Lenz, V., &amp; Krause, T., 2015: 10). We cannot entirely know what people are doing with news in private messaging networks, but what we can see is what the media and journalists are doing with these platforms. This report is a draft of these actions.</p>
    <p>In news sharing research, a new broad theoretical foundation is needed, with quantitative studies, digital ethnographies or uses and gratifications approaches, and even combining these theories and deriving new ones. We utilize the results of this preliminary research to provide insights so that journalism can be improved, and academic research of journalism can move forward in news sharing research.</p>
    <p>The main goal of this executive report is to help journalists and researchers to get a deeper understanding of the news sharing processes in private messaging apps, channels, and networks. Share it, but not in a private way. Make it as public as you can.</p>
  </div>
  <svg class="wave"><use href="#footer-wave"/></svg>
  <div class="footer"><span>THE (PRIVATE) NEWS <b>SHARING REPORT</b></span><span>PAGE - 4</span></div>
</article>

<div class="label" style="left:108px;top:2308px">INNER PAGE 2</div>
<div class="label" style="left:615px;top:2308px">INNER PAGE 3</div>

<!-- row 3 -->
<article class="page" style="left:117px;top:2364px">
  <div class="rule"></div>
  <div class="heading" style="left:85px;top:116px">THE INTERVIEWS</div>
  <div class="text" style="left:82px;top:160px;width:345px;font-size:7.6px">
    <p>All the interviews represent the journalists' personal point of view and they are not necessarily the official opinion of the media and institutions where they work. Because of the design of this report, the questions were deleted but you can easily figure out the kind of questions by reading the selected answers.</p>
  </div>
  <div style="position:absolute;left:82px;top:242px;font-family:'Poppins',sans-serif;font-weight:700;font-size:8.5px;color:var(--ink)">INDEX OF INTERVIEWS</div>
  <ul class="toc plain" style="left:78px;width:352px;top:264px">
    <li style="background:none"><span>1. Clara Westbrook, The Global Forum for Reporters, SeedNews Ambassador<br>&nbsp;&nbsp;&nbsp;at the USA.</span></li>
    <li style="background:var(--row)"><span>2. Irene Solis Marquez, Audience Engagement Editor at The Center for Open Accountability.</span></li>
    <li style="background:none"><span>3. Lucía Ferrer, Operations Editor at The Harbor Ledger.</span></li>
    <li style="background:var(--row)"><span>4. Jordi Valls, journalist, Meridian Media Network.</span></li>
    <li style="background:none"><span>5. Daniel Hawthorne, journalist, The Iberia Brief.</span></li>
    <li style="background:var(--row)"><span>6. Marta Olmedo, digital journalist, Sol Noticias.</span></li>
    <li style="background:none"><span>7. Iván Castro, Head of Content at Factora.</span></li>
    <li style="background:var(--row)"><span>8. Sergio Alba, journalist, Project Consultant at Verdad Lab.</span></li>
  </ul>
  <svg class="wave"><use href="#footer-wave"/></svg>
  <div class="footer"><span>THE (PRIVATE) NEWS <b>SHARING REPORT</b></span><span>PAGE - 5</span></div>
</article>

<article class="page" style="left:624px;top:2364px">
  <div class="photo" role="img" aria-label="Portrait photograph of the interviewee"></div>
  <div class="person">CLARA WESTBROOK</div>
  <div class="role">Journalist, The Global Forum for Reporters (GFR), GFR Media Fellows<br>&amp; SeedNews Ambassador at the USA - @ClaraWestB</div>
  <div class="quote"><span class="mark">“</span> Media should develop relationships of trust, audience can have a greater sense of trust with messaging privately <span class="mark">”</span></div>
  <div class="text" style="left:85px;top:302px;width:335px;font-size:7.6px">
    <div class="subhead">FACT-CHECKING AS A MODEL</div>
    <p>Fact-checking is an important component for media organizations to incorporate now and going forward. However, I think that the approach to incorporating fact-checking into news organizations needs to be different for every newsroom. Newsrooms have varying sizes, focuses and specialties, and I do not think that all newsrooms have the capacity to function as fact-checking organizations equally. It is helpful for some news organizations to be leaders in fact-checking and others can learn from those organizations. For example, Verifica in Andoria is a pioneer and a resource in regards to fact-checking, not all organizations can fact-check at the deep level that Verifica does.</p>
    <div class="subhead">STARTING A JOURNALISTIC PROJECT</div>
    <p>Fact-checking is an important component for media organizations to incorporate now and going forward. However, I think that the approach to incorporating fact-checking into news organizations needs to be different for every newsroom. Newsrooms have varying sizes, focuses and specialties, and I do not think that all newsrooms have the capacity to function as fact-checking organizations equally. It is helpful for some news organizations to be leaders in fact-checking and others can learn from those organizations. For example, Verifica in Andoria is a pioneer and a resource in regards to fact-checking, not all organizations can fact-check at the deep level that Verifica does.</p>
  </div>
  <svg class="wave"><use href="#footer-wave"/></svg>
  <div class="footer"><span>THE (PRIVATE) NEWS <b>SHARING REPORT</b></span><span>PAGE - 6</span></div>
</article>

<div class="label" style="left:117px;top:3088px">INNER PAGE 4</div>
<div class="label" style="left:624px;top:3088px">INNER PAGE 5</div>

<!-- row 4 -->
<article class="page" style="left:355px;top:3140px">
  <div class="rule"></div>
  <div class="text" style="left:85px;top:178px;width:335px;font-size:7.6px">
    <p>Looking for diversified sources of revenue is also an important area in which to develop when starting a digital project on one's own. Putting together a team with diverse strengths will also help with finding different revenue sources and having a solid project overall. For example, at SeedNews, we like to remind people that they should probably not start an independent media organization with a team exclusively comprised of reporters. In addition to those journalists, there should be someone with more experience in business/finance, so that someone on the team is able to help guide everyone on how to run the media organization as a business.</p>
    <div class="subhead">PRIVATE NETWORKS</div>
    <p>Private networks are something that media organizations all over the world are exploring, especially organizations with niche audiences or organizations trying to reach audiences where misinformation spreads rapidly.</p>
    <div class="subhead">TEACHING MEDIA LITERACY</div>
    <p>I do think media organizations have a role to play as far as teaching their audiences media literacy. While I do not think many audience members will want to take the time to fact-check information themselves, I think media organizations should develop relationships of trust with their audience members. If there is trust between a media organization and its audience, the audience will feel more comfortable coming to journalists with questions and will be receptive to fact-checked information from that media organization.</p>
    <div class="subhead">MORE TRUST</div>
    <p>I do think media organizations have a role to play as far as teaching their audiences media literacy. While I do not think many audience members will want to take the time to fact-check information themselves, I think media organizations should develop relationships of trust with their audience members. If there is trust between a media organization and its audience, the audience will feel more comfortable coming to journalists with questions and will be receptive to fact-checked information from that media organization.</p>
  </div>
  <svg class="wave"><use href="#footer-wave"/></svg>
  <div class="footer"><span>THE (PRIVATE) NEWS <b>SHARING REPORT</b></span><span>PAGE - 7</span></div>
</article>

<div class="label" style="left:355px;top:3864px">INNER PAGE 6</div>

</body>
</html>
```